SkyvornQ Business Cards and Stationary Design

Need a design for our business cards and stationary. I want to carry on the theme of the logo. I want the business cards to have a design on the back. I would like the business cards and the stationary to carry the same theme, design scheme, and branding

Target Market(s)

Airlines and Maintenance Facilities

Industry/Entity Type

Aviation

Contact Information for Business Card

Name
Position Title
Address: 4827 Trellis Hollow Road, Fort Pierce, Florida, 34951
Office Number
Mobile Number
Email
Website

Font styles to use
Serif
Sans Serif

Colors

Designer to choose colors to be used in the design.

```html
<!DOCTYPE html>
<html lang="en">
<head>
<meta charset="utf-8">
<title>SkyvornQ Business Card</title>
<link rel="stylesheet" href="https://fonts.googleapis.com/css2?family=Roboto:wght@400;500&family=Roboto+Condensed:wght@700&display=swap">
<style>
  :root {
    --navy: #0b2a55;
    --navy-deep: #06224a;
    --sky: #1f9be0;
    --blue-mid: #1d5fae;
    --ink: #5a6472;
    --paper: #f4f5f6;
    --backdrop: #e7e9ec;
    --white: #ffffff;
  }
  * { margin: 0; padding: 0; box-sizing: border-box; }
  html, body { width: 1200px; height: 950px; overflow: hidden; }
  body {
    background: var(--backdrop);
    font-family: "Roboto", Arial, sans-serif;
    position: relative;
  }
  .card {
    position: absolute;
    left: 270px;
    width: 660px;
    height: 380px;
    border-radius: 26px;
    overflow: hidden;
    box-shadow: 0 10px 26px rgba(0,0,0,0.18);
  }
  .card-front { top: 60px; background: var(--paper); }
  .card-back { top: 510px; background: var(--navy-deep); }

  .swoosh { position: absolute; inset: 0; }

  .brand {
    position: absolute;
    left: 52px;
    top: 120px;
    display: flex;
    align-items: center;
    gap: 16px;
  }
  .brand-dot {
    width: 34px; height: 34px;
    border-radius: 50%;
    background: var(--blue-mid);
  }
  .brand-name {
    font-family: "Roboto", Arial, sans-serif;
    font-weight: 500;
    font-size: 38px;
    letter-spacing: 9px;
    color: var(--navy);
  }

  .contact {
    position: absolute;
    left: 54px;
    top: 196px;
    list-style: none;
    font-size: 16px;
    line-height: 23px;
    color: var(--ink);
  }
  .contact li { display: flex; align-items: center; gap: 10px; }
  .contact .address { padding-left: 0; }
  .contact svg { width: 13px; height: 13px; flex: none; fill: var(--navy); }

  .person {
    position: absolute;
    right: 40px;
    top: 150px;
    text-align: right;
    font-family: "Roboto Condensed", "Arial Narrow", sans-serif;
    font-weight: 700;
    text-transform: uppercase;
  }
  .person-name { font-size: 27px; color: var(--navy); line-height: 30px; }
  .person-title { font-size: 19px; color: var(--sky); line-height: 22px; }

  .back-site {
    position: absolute;
    left: 34px;
    top: 50%;
    transform: translate(-50%, -50%) rotate(90deg);
    transform-origin: center;
    margin-left: 10px;
    font-size: 14px;
    letter-spacing: 6px;
    color: var(--white);
    white-space: nowrap;
  }
  .back-brand {
    position: absolute;
    left: 50%; top: 50%;
    transform: translate(-50%, -50%);
    display: flex;
    align-items: center;
    gap: 18px;
  }
  .back-brand .brand-dot { width: 40px; height: 40px; background: var(--white); }
  .back-brand .brand-name { color: var(--white); font-size: 44px; }
</style>
</head>
<body>

<section class="card card-front">
  <svg class="swoosh" viewBox="0 0 660 380" preserveAspectRatio="none" aria-hidden="true">
    <defs>
      <linearGradient id="swooshFill" x1="0" y1="0" x2="1" y2="1">
        <stop offset="0" stop-color="#0a2e63"/>
        <stop offset="0.6" stop-color="#1d5fae"/>
        <stop offset="1" stop-color="#0b2a55"/>
      </linearGradient>
    </defs>
    <path d="M250 0 H660 V118 C570 48 430 14 250 0 Z" fill="url(#swooshFill)"/>
    <path d="M290 0 C450 20 580 60 660 138 L660 128 C575 56 455 20 310 0 Z" fill="#0b2a55"/>
  </svg>

  <div class="brand">
    <span class="brand-dot"></span>
    <span class="brand-name">SKYVORNQ</span>
  </div>

  <ul class="contact">
    <li class="address">4827 Trellis Hollow Road</li>
    <li class="address">Fort Pierce, Florida, 34951</li>
    <li><svg viewBox="0 0 16 16"><path d="M3.5 1 L6 1 L7 5 L5.3 6.3 C6.2 8.3 7.7 9.8 9.7 10.7 L11 9 L15 10 L15 12.5 C15 13.9 13.9 15 12.5 15 C6.7 15 1 9.3 1 3.5 C1 2.1 2.1 1 3.5 1 Z"/></svg>772 514 3086</li>
    <li><svg viewBox="0 0 16 16"><path d="M4 0 H12 A1 1 0 0 1 13 1 V15 A1 1 0 0 1 12 16 H4 A1 1 0 0 1 3 15 V1 A1 1 0 0 1 4 0 Z M5 2 V13 H11 V2 Z"/></svg>772 903 6217</li>
    <li><svg viewBox="0 0 16 16"><path d="M0 3 H16 V13 H0 Z M1.5 4.5 V5 L8 9 L14.5 5 V4.5 Z"/></svg>info@skyvornq.com</li>
    <li><svg viewBox="0 0 16 16"><circle cx="8" cy="8" r="7.5"/></svg>www.skyvornq.com</li>
  </ul>

  <div class="person">
    <p class="person-name">Daniel Harlow</p>
    <p class="person-title">CEO/Founder</p>
  </div>
</section>

<section class="card card-back">
  <p class="back-site">www.skyvornq.com</p>
  <div class="back-brand">
    <span class="brand-dot"></span>
    <span class="brand-name">SKYVORNQ</span>
  </div>
</section>

</body>
</html>
```